Stationery Set for Velmora Company

I need to create full stationery design for my company; Business Cards, Envelops, Letter Heads, Calendar.
In the letter head and Envelops... only contact information and website links.
Our company is a Service Management company with different domains of innovative services including Technology Service Management, Education Services, Outsourcing Management, Events Management.
I need a modern and innovative design specially for the business card. I some transparent designs and I like it, but don't limit your innovation to what I mentioned. Sky is limit for your innovation.

Target Market(s)

Middle East & Africa

Industry/Entity Type

Business Management

Colors
34a7d8
0355a3
85acd3
86cae7
cee9f5
cfdeed
e4daeb
f3f1f8
ecf7fb

Requirements
Must have
• Name, Title, Email, Mobile
Nice to have
• We have multiple locations in USA, KSA, EGY, so I need ideas about how to include all contact details maybe QR / Barcode or something else.
• Please see our locations and contact information: www.brightvelmora.example
Should not have
• Too much text

```html
<!DOCTYPE html>
<html lang="en">
<head>
<meta charset="utf-8">
<title>Velmora Company Stationery Set</title>
<link href="https://fonts.googleapis.com/css2?family=Arimo:wght@400;700&display=swap" rel="stylesheet">
<style>
:root{
  --bg:#eceef0;
  --paper:#ffffff;
  --navy:#0355a3;
  --royal:#2a4fb4;
  --sky:#34a7d8;
  --pale-sky:#86cae7;
  --mist:#cee9f5;
  --ink:#3a3a3a;
  --grey:#8a8d91;
}
*{margin:0;padding:0;box-sizing:border-box}
html,body{width:1200px;height:937px;overflow:hidden}
body{background:var(--bg);font-family:"Arimo",Arial,sans-serif;color:var(--ink);position:relative}
.piece{position:absolute;background:var(--paper);overflow:hidden}
.piece svg.art{position:absolute;left:0;top:0}
.brand{position:absolute;font-weight:700;color:var(--navy);letter-spacing:.5px;line-height:1}
.brand::before{content:"";display:inline-block;width:.55em;height:.55em;border-radius:50%;background:var(--navy);margin-right:.25em;vertical-align:.05em}

/* Letterhead */
.letterhead{left:185px;top:68px;width:385px;height:544px}
.letterhead .brand{left:20px;top:26px;font-size:20px}
.letter-body{position:absolute;left:37px;top:138px;width:250px;font-size:5.6px;line-height:8px;color:#555}
.letter-body p{margin-bottom:10px}
.letter-body .strong{font-weight:700;color:#333;margin-bottom:0}
.letter-body .signature{width:36px;height:18px;margin:4px 0 8px;border-radius:3px;background:linear-gradient(90deg,#e2e4e7,#f1f2f4)}
.letter-contact{position:absolute;right:10px;top:460px;text-align:right;font-size:5.4px;line-height:9px;color:#fff}
.letter-contact .gap{height:8px}

/* Folder cover */
.folder{left:636px;top:41px;width:456px;height:575px}
.folder .brand{left:24px;top:432px;font-size:40px}
.folder-web{position:absolute;left:22px;top:550px;font-size:10px;letter-spacing:2.4px;color:#222;font-weight:700}

/* Business cards */
.card-front{left:46px;top:659px;width:175px;height:99px}
.card-name{position:absolute;right:8px;top:8px;text-align:right;font-size:6.5px;font-weight:700;color:#333;line-height:7px}
.card-name small{display:block;font-size:4.4px;font-weight:400}
.card-contact{position:absolute;right:8px;top:33px;text-align:right;font-size:3.6px;line-height:6px;color:#444}
.card-front .brand{left:22px;top:80px;font-size:10px}
.card-back{left:46px;top:784px;width:175px;height:99px}
.card-back .brand{left:10px;top:62px;font-size:14px}

/* Envelopes */
.envelope{left:265px;top:672px;width:431px;height:207px}
.envelope .brand{left:16px;top:28px;font-size:18px}
.envelope-back{left:737px;top:672px;width:431px;height:207px}
.flap-web{position:absolute;left:0;top:28px;width:100%;text-align:center;font-size:10px;letter-spacing:2.6px;color:#fff}
</style>
</head>
<body>

<section class="piece letterhead" aria-label="Letterhead">
  <svg class="art" width="385" height="544" viewBox="0 0 385 544">
    <defs>
      <linearGradient id="lh-band" x1="0" y1="1" x2="1" y2="0">
        <stop offset="0" stop-color="#1d47b0"/>
        <stop offset="1" stop-color="#2f68c9"/>
      </linearGradient>
      <linearGradient id="lh-sky" x1="0" y1="0" x2="1" y2="0">
        <stop offset="0" stop-color="#86cae7" stop-opacity="0"/>
        <stop offset="1" stop-color="#34a7d8"/>
      </linearGradient>
    </defs>
    <path d="M10,530 C150,500 280,450 385,385 L385,420 C280,470 170,510 10,530 Z" fill="url(#lh-sky)" opacity=".6"/>
    <path d="M70,544 C190,515 300,470 385,420 L385,544 Z" fill="url(#lh-band)"/>
    <path d="M90,544 C210,518 310,478 385,440" stroke="#86cae7" stroke-width="2" fill="none" opacity=".7"/>
  </svg>
  <div class="brand">Velmora</div>
  <div class="letter-body">
    <p>July 2, 2012</p>
    <p class="strong">Dear Cli,</p>
    <p>ABC Building, def St., Country Name</p>
    <p>We are pleased to share an update on our service programmes across the region. Our teams continue to support clients in technology, education, outsourcing and events with care and attention to detail.</p>
    <p>Please find the enclosed summary of the next quarter plan and schedule.</p>
    <p style="margin-top:22px">We look forward to working with you and welcome any questions about the proposal. Our office team is ready to arrange a meeting at a time that suits you.</p>
    <p>Best Regards,</p>
    <div class="signature" role="img" aria-label="Handwritten signature of the director"></div>
    <p class="strong">Daniel Roe</p>
    <p style="margin-bottom:4px">Director</p>
    <p>ABC Building, def St., Country Name</p>
  </div>
  <div class="letter-contact">
    12 Harbor Street<br>North Road
    <div class="gap"></div>
    010 555 0148 &#9742;<br>010 555 0149 &#9742;<br>010 555 0150 &#9993;
    <div class="gap"></div>
    hello@brightvelmora.example<br>www.brightvelmora.example
  </div>
</section>

<section class="piece folder" aria-label="Folder cover">
  <svg class="art" width="456" height="575" viewBox="0 0 456 575">
    <defs>
      <linearGradient id="fo-band" x1="0" y1="0" x2="0" y2="1">
        <stop offset="0" stop-color="#2a4fb4"/>
        <stop offset=".5" stop-color="#3b73d0"/>
        <stop offset="1" stop-color="#2a4fb4"/>
      </linearGradient>
      <linearGradient id="fo-glow" x1="0" y1="0" x2="0" y2="1">
        <stop offset="0" stop-color="#34a7d8" stop-opacity=".9"/>
        <stop offset=".6" stop-color="#86cae7" stop-opacity=".5"/>
        <stop offset="1" stop-color="#cee9f5" stop-opacity="0"/>
      </linearGradient>
    </defs>
    <path d="M112,0 L175,0 C190,120 270,210 340,300 C250,230 150,170 112,0 Z" fill="url(#fo-glow)"/>
    <path d="M72,0 L112,0 C140,120 260,200 330,300 C400,400 440,480 456,555 L456,575 L438,575 C420,470 362,360 292,272 C200,160 92,120 72,0 Z" fill="url(#fo-band)"/>
    <path d="M112,0 C150,130 280,210 345,310 C405,405 436,480 450,575 L438,575 C420,470 362,360 292,272 C210,170 120,120 112,0 Z" fill="#86cae7" opacity=".55"/>
  </svg>
  <div class="brand">Velmora</div>
  <div class="folder-web">www.brightvelmora.example</div>
</section>

<section class="piece card-front" aria-label="Business card front">
  <svg class="art" width="175" height="99" viewBox="0 0 175 99">
    <defs>
      <linearGradient id="bc-blue" x1="0" y1="0" x2="1" y2="1">
        <stop offset="0" stop-color="#2a4fb4"/>
        <stop offset="1" stop-color="#34a7d8"/>
      </linearGradient>
    </defs>
    <path d="M0,0 L120,0 C90,20 50,45 0,82 Z" fill="url(#bc-blue)"/>
    <path d="M0,88 C40,52 90,22 130,0 L140,0 C100,24 50,55 0,95 Z" fill="#86cae7" opacity=".6"/>
  </svg>
  <div class="card-name">ADAM HALE<small>DIRECTOR</small></div>
  <div class="card-contact">12 Harbor Street<br>North Road<br>010 555 0148 &#9742;<br>010 555 0149 &#9742;<br>hello@brightvelmora.example<br>www.brightvelmora.example</div>
  <div class="brand">Velmora</div>
</section>

<section class="piece card-back" aria-label="Business card back">
  <svg class="art" width="175" height="99" viewBox="0 0 175 99">
    <defs>
      <linearGradient id="cb-curl" x1="0" y1="0" x2="1" y2="0">
        <stop offset="0" stop-color="#3d3d3d"/>
        <stop offset="1" stop-color="#e6e6e6"/>
      </linearGradient>
    </defs>
    <path d="M112,0 L132,0 C136,25 150,45 175,55 L175,70 C140,60 116,35 112,0 Z" fill="url(#cb-curl)"/>
  </svg>
  <div class="brand">Velmora</div>
</section>

<section class="piece envelope" aria-label="Envelope front">
  <svg class="art" width="431" height="207" viewBox="0 0 431 207">
    <defs>
      <linearGradient id="en-curl" x1="0" y1="0" x2="1" y2="0">
        <stop offset="0" stop-color="#3a3a3a"/>
        <stop offset=".5" stop-color="#9a9a9a"/>
        <stop offset="1" stop-color="#efefef"/>
      </linearGradient>
    </defs>
    <path d="M290,0 L335,0 C342,55 380,92 431,102 L431,128 C370,112 300,70 290,0 Z" fill="url(#en-curl)"/>
  </svg>
  <div class="brand">Velmora</div>
</section>

<section class="piece envelope-back" aria-label="Envelope back">
  <svg class="art" width="431" height="207" viewBox="0 0 431 207">
    <defs>
      <linearGradient id="eb-flap" x1="0" y1="0" x2="1" y2="0">
        <stop offset="0" stop-color="#2a4fb4"/>
        <stop offset=".6" stop-color="#2f6fcf"/>
        <stop offset="1" stop-color="#34a7d8"/>
      </linearGradient>
    </defs>
    <path d="M0,0 L431,0 L431,44 Q431,72 403,72 L28,72 Q0,72 0,44 Z" fill="url(#eb-flap)"/>
  </svg>
  <div class="flap-web">www.brightvelmora.example</div>
</section>

</body>
</html>
```